Harborline Renewal Business Card Design

Professional and clean design. The design colors should flow with the logo. Two-sided card with the website on the back which is:

www.HarborlineRenewal.example.

"Specializing in Water Damage Restoration"

On the front I need the name, email, phone, and logo.

Name: Darnell Quisby
Email: Darnell@HarborlineRenewal.example
Phone: 555-318-2046 for now

I only have the Preview and Thumbnail right now but should have the source files uploaded within a day or two.

Target Market(s)

Flood victims, home owners with water damage from busted pipes etc...

Industry/Entity Type

Business

Contact Information for Business Card

Name: Darnell Quisby

Font styles to use
Serif
Sans Serif

Requirements
Must have
• Business Card Details Info

```html
<!DOCTYPE html>
<html lang="en">
<head>
<meta charset="utf-8">
<title>Harborline Renewal Business Card</title>
<link href="https://fonts.googleapis.com/css2?family=Open+Sans:wght@400;600;700&display=swap" rel="stylesheet">
<style>
  :root {
    --backdrop: #2a2a2a;
    --card: #ffffff;
    --blue: #2b97d6;
    --blue-deep: #1f86c8;
    --blue-light: #56bff0;
  }
  * { box-sizing: border-box; margin: 0; padding: 0; }
  html, body { width: 1200px; height: 900px; overflow: hidden; }
  body {
    background: var(--backdrop);
    font-family: "Open Sans", Arial, sans-serif;
    position: relative;
  }
  .card {
    position: absolute;
    left: 290px;
    width: 620px;
    height: 354px;
    background: var(--card);
    border-radius: 22px;
    overflow: hidden;
  }
  .card-back { top: 56px; }
  .card-front { top: 478px; }

  /* back side */
  .back-brand {
    position: absolute;
    top: 92px; left: 0; right: 0;
    display: flex; align-items: center; justify-content: center; gap: 16px;
  }
  .brand-dot {
    width: 58px; height: 58px; border-radius: 50%;
    background: var(--blue-light);
  }
  .brand-name {
    color: var(--blue);
    font-weight: 600;
    font-size: 30px;
    letter-spacing: 0.5px;
  }
  .tagline {
    position: absolute; top: 232px; left: 0; right: 0;
    text-align: center; color: var(--blue);
    font-size: 15px; letter-spacing: 0.4px; text-transform: uppercase;
  }
  .back-web {
    position: absolute; top: 260px; left: 0; right: 0;
    text-align: center; color: var(--blue); font-size: 15px;
  }

  /* front side */
  .front-brand {
    position: absolute; top: 38px; left: 36px;
    display: flex; align-items: center; gap: 12px;
  }
  .front-brand .brand-dot { width: 44px; height: 44px; }
  .front-brand .brand-name { font-size: 24px; }
  .holder-name {
    position: absolute; top: 112px; right: 62px;
    color: var(--blue-deep); font-weight: 700; font-size: 24px;
    letter-spacing: 0.5px; text-transform: uppercase;
  }
  .name-rule {
    position: absolute; top: 150px; left: 260px; right: 40px;
    height: 2px; background: var(--blue);
  }
  .name-cap {
    position: absolute; top: 133px; right: -14px;
    width: 36px; height: 36px; border-radius: 50%;
    border: 3px solid var(--blue-light); background: var(--card);
  }
  .contact-rule {
    position: absolute; top: 218px; left: 36px; width: 310px;
    height: 1.5px; background: var(--blue);
  }
  .contact-list {
    position: absolute; top: 226px; left: 40px;
    list-style: none; color: var(--blue-deep); font-size: 15px; line-height: 22px;
  }
  .contact-list li { display: flex; align-items: center; gap: 8px; }
  .contact-list svg { width: 12px; height: 12px; flex: none; }
  .band { position: absolute; left: 0; bottom: 0; width: 620px; height: 80px; }
</style>
</head>
<body>
  <section class="card card-back">
    <div class="back-brand">
      <span class="brand-dot"></span>
      <span class="brand-name">Harborline Renewal</span>
    </div>
    <p class="tagline">Specializing in Water Damage Restoration</p>
    <p class="back-web">www.HarborlineRenewal.example</p>
  </section>

  <section class="card card-front">
    <div class="front-brand">
      <span class="brand-dot"></span>
      <span class="brand-name">Harborline Renewal</span>
    </div>
    <h1 class="holder-name">Darnell Quisby</h1>
    <div class="name-rule"></div>
    <div class="name-cap"></div>
    <div class="contact-rule"></div>
    <ul class="contact-list">
      <li><svg viewBox="0 0 12 12"><path d="M2.5 1l2 2.2-1 1.3c.7 1.5 2 2.8 3.5 3.5l1.3-1 2.2 2-1 1.6C5 10.5 1.5 7 .9 2z" fill="var(--blue)"/></svg>555-318-2046</li>
      <li><svg viewBox="0 0 12 12"><rect x="0.8" y="2.2" width="10.4" height="7.6" fill="none" stroke="var(--blue)" stroke-width="1.3"/><path d="M1 2.6l5 4 5-4" fill="none" stroke="var(--blue)" stroke-width="1.3"/></svg>Darnell@HarborlineRenewal.example</li>
      <li><svg viewBox="0 0 12 12"><circle cx="6" cy="6" r="5" fill="none" stroke="var(--blue)" stroke-width="1.2"/><path d="M1 6h10M6 1c-2.5 3-2.5 7 0 10M6 1c2.5 3 2.5 7 0 10" fill="none" stroke="var(--blue)" stroke-width="1"/></svg>www.HarborlineRenewal.example</li>
    </ul>
    <svg class="band" viewBox="0 0 620 80" aria-hidden="true">
      <path d="M0 62 L330 62 C360 62 370 34 400 34 L620 34 L620 80 L0 80 Z" fill="var(--blue)"/>
      <circle cx="395" cy="50" r="13" fill="none" stroke="#ffffff" stroke-width="2.5"/>
    </svg>
  </section>
</body>
</html>
```